Tech business card design

We need an amazing business card design for our new business 'Pexla' a marketing tech startup based in Sydney, Australia. We provide an online marketplace for businesses to search and buy advertising media, connect with service providers and learn more about marketing. We wish to communicate 'cool tech', reliability and professionalism and design based around our logo.

Target Market(s)

Business Owners

Contact Information for Business Card

Name
Position
Email Address
Website
Phone Number

Font styles to use
Other font styles liked:
• Avenir & Avenir Next

Colors

Designer to choose colors to be used in the design.

```html
<!DOCTYPE html>
<html lang="en">
<head>
<meta charset="utf-8">
<title>Pexla business card</title>
<link rel="stylesheet" href="https://fonts.googleapis.com/css2?family=Mulish:wght@400;600;900&display=swap">
<style>
  :root {
    --bg: #efe7e7;
    --paper: #f7f7f6;
    --navy: #34345f;
    --navy-deep: #2e2e57;
    --teal: #5fb3c0;
    --ink: #3b3b4a;
    --photo-a: #9aa3b4;
    --photo-b: #5c6385;
  }
  * { box-sizing: border-box; margin: 0; padding: 0; }
  html, body {
    width: 1200px; height: 858px; overflow: hidden;
    background: var(--bg);
    font-family: "Mulish", sans-serif;
  }
  .stage {
    position: relative; width: 1200px; height: 858px;
  }
  .card {
    position: absolute; top: 280px;
    width: 520px; height: 297px;
    border-radius: 4px;
    box-shadow: 0 10px 26px rgba(60, 40, 50, .14);
    overflow: hidden;
  }
  .card--front { left: 50px; background: var(--paper); }
  .card--back { left: 630px; background: var(--navy); }

  .wordmark {
    font-family: "Mulish", sans-serif;
    font-weight: 900;
    letter-spacing: -1px;
    line-height: 1;
  }
  .card--front .wordmark {
    position: absolute; left: 44px; top: 64px;
    font-size: 64px; color: var(--navy);
  }

  .contact {
    position: absolute; left: 282px; top: 132px;
    color: var(--ink);
  }
  .contact__name {
    font-size: 17px; font-weight: 600; letter-spacing: .5px;
    color: var(--navy);
  }
  .contact__name span { color: var(--teal); }
  .contact__role {
    display: inline-block; margin-top: 3px;
    padding: 3px 40px 3px 8px;
    font-size: 11px; color: #fff;
    background: linear-gradient(90deg, var(--navy), var(--teal));
  }
  .contact__list { list-style: none; margin-top: 8px; }
  .contact__item {
    display: flex; align-items: center; gap: 8px;
    font-size: 12px; line-height: 18px;
  }
  .contact__item svg { width: 11px; height: 11px; flex: none; }

  .card__photo { position: absolute; left: 0; top: 0; }
  .card--back .wordmark {
    position: absolute; right: 58px; bottom: 62px;
    font-size: 62px; color: #fff;
  }
  .card__url {
    position: absolute; right: 118px; bottom: 48px;
    font-size: 11px; color: var(--teal); letter-spacing: .3px;
  }
</style>
</head>
<body>
<main class="stage">

  <section class="card card--front" aria-label="Business card front">
    <div class="wordmark">pexla</div>
    <div class="contact">
      <p class="contact__name">DANA <span>MORROW</span></p>
      <p class="contact__role">Founder | Director</p>
      <ul class="contact__list">
        <li class="contact__item">
          <svg viewBox="0 0 12 12" aria-hidden="true"><rect x="3" y="0.5" width="6" height="11" rx="1" fill="none" stroke="#3b3b4a"/><circle cx="6" cy="9.6" r=".7" fill="#3b3b4a"/></svg>
          +61 (0)412 555 018
        </li>
        <li class="contact__item">
          <svg viewBox="0 0 12 12" aria-hidden="true"><rect x="0.5" y="2" width="11" height="8" fill="#3b3b4a"/><path d="M1 2.5 6 6.5 11 2.5" fill="none" stroke="#fff"/></svg>
          dana@pexlamedia.com.au
        </li>
        <li class="contact__item">
          <svg viewBox="0 0 12 12" aria-hidden="true"><circle cx="6" cy="6" r="5.5" fill="#3b3b4a"/><path d="M.5 6h11M6 .5c-3 3-3 8 0 11M6 .5c3 3 3 8 0 11" fill="none" stroke="#fff" stroke-width=".7"/></svg>
          www.pexlamedia.com.au
        </li>
      </ul>
    </div>
  </section>

  <section class="card card--back" aria-label="Business card back">
    <svg class="card__photo" width="520" height="297" viewBox="0 0 520 297">
      <defs>
        <linearGradient id="photoTone" x1="0" y1="0" x2="1" y2="1">
          <stop offset="0" stop-color="var(--photo-a)"/>
          <stop offset="1" stop-color="var(--photo-b)"/>
        </linearGradient>
      </defs>
      <path role="img" aria-label="Photo of a hand working on a tablet"
            d="M0 0H238Q262 0 258 26L240 150Q236 176 210 172L0 140Z"
            fill="url(#photoTone)"/>
      <path d="M238 0Q262 0 258 26L240 150Q236 176 210 172L0 140"
            fill="none" stroke="#fff" stroke-width="5"/>
    </svg>
    <div class="wordmark">pexla</div>
    <p class="card__url">www.pexlamedia.com.au</p>
  </section>

</main>
</body>
</html>
```